Namibia currently imports 60% of its food. Harvest Crest Oruva is an initiative which will assist Namibia to become self sustainable in terms of food production. We aim to do this through the development of 3 agricultural production zones which will include farming zones, local farmer assistance, processing and distribution of the final products. Please see our project overview attached.

```html
<!DOCTYPE html>
<html lang="en">
<head>
<meta charset="utf-8">
<title>Sustainability – Harvest Crest Oruva</title>
<link href="https://fonts.googleapis.com/css2?family=Merriweather:wght@400;700&family=Noto+Serif:wght@400;700&family=Tinos&display=swap" rel="stylesheet">
<style>
:root{
  --green:#0b6b3a;
  --tan:#c4a27e;
  --text:#3d3d3d;
  --white:#ffffff;
  --card-border:#dfeee8;
  --photo-warm:#8a8a5e;
  --photo-leaf:#5e8a34;
  --photo-soft:#b9b8a4;
}
*{margin:0;padding:0;box-sizing:border-box}
html,body{width:1200px;height:2474px;overflow:hidden;background:var(--white)}
body{position:relative;font-family:"Noto Serif",Georgia,serif;color:var(--text)}
.abs{position:absolute}

/* header */
.brand{left:111px;top:62px;display:flex;align-items:center;gap:12px}
.brand-dot{width:16px;height:16px;border-radius:50%;background:var(--tan)}
.brand-name{font-family:"Merriweather",Georgia,serif;font-size:27px;font-weight:400;color:var(--green);letter-spacing:.5px}
.contact{display:flex;align-items:flex-start;gap:18px}
.contact-icon{width:48px;height:48px;border-radius:50%;background:var(--green);display:flex;align-items:center;justify-content:center;margin-top:3px}
.contact-label{font-family:"Merriweather",Georgia,serif;font-weight:700;font-size:16px;color:var(--green)}
.contact-value{font-size:19px;color:var(--text);margin-top:4px;padding-left:6px}
.call{left:586px;top:26px}
.mail{left:885px;top:26px}
.nav{top:112px;font-family:"Tinos","Times New Roman",serif;font-size:15px;color:var(--text)}
.nav.active{color:var(--tan)}
.nav.active::after{content:"";position:absolute;left:22px;right:22px;bottom:-7px;height:2px;background:var(--tan)}

/* hero */
.hero{left:0;top:140px;width:1200px;height:520px;
  background:
   linear-gradient(180deg,#fff 0%,rgba(255,255,255,0) 16%),
   linear-gradient(90deg,#7d6c4e 0%,#7a7a48 40%,#5f8f38 70%,#76a83e 100%)}
.hero-kicker{left:108px;top:308px;font-family:"Merriweather",Georgia,serif;font-weight:700;font-size:28px;color:var(--white)}
.hero-title{left:108px;top:360px;font-family:"Merriweather",Georgia,serif;font-weight:700;font-size:54px;color:var(--white)}
.play{left:828px;top:356px;width:58px;height:58px;border-radius:50%;background:var(--green);box-shadow:0 0 0 4px rgba(255,255,255,.35);display:flex;align-items:center;justify-content:center}

/* intro */
.section-title{left:0;width:1200px;top:736px;text-align:center;font-family:"Merriweather",Georgia,serif;font-weight:700;font-size:48px;color:var(--green)}
.rule{left:552px;top:810px;width:96px;height:3px;background:var(--tan)}
.photo{border-radius:5px;background:linear-gradient(180deg,var(--photo-soft) 0%,var(--photo-warm) 50%,var(--photo-leaf) 100%)}
.photo-one{left:111px;top:856px;width:489px;height:293px}
.photo-two{left:600px;top:1208px;width:488px;height:292px}
.sub-heading{font-family:"Merriweather",Georgia,serif;font-weight:700;font-size:32px;color:var(--tan)}
.copy{font-size:16px;line-height:26px;color:var(--text);letter-spacing:-.15px}
.solutions-title{left:677px;top:850px}
.solutions-copy{left:677px;top:912px;width:425px}
.processing-title{left:113px;top:1209px}
.processing-copy{left:113px;top:1271px;width:410px}
.yields-title{left:113px;top:1472px;font-family:"Merriweather",Georgia,serif;font-weight:700;font-size:22px;color:var(--green)}

/* yields */
.field{left:0;top:1517px;width:1200px;height:537px;
  background:linear-gradient(180deg,#fff 0%,#fff 22%,#c9d9a1 38%,#7fa23c 52%,#5e8a2c 72%,#3f6422 100%)}
.card{top:1560px;width:303px;height:281px;background:var(--white);border:2px solid var(--card-border);border-radius:12px;box-shadow:0 4px 14px rgba(0,0,0,.08);text-align:center}
.card svg{margin-top:56px}
.card-title{font-family:"Merriweather",Georgia,serif;font-weight:700;font-size:28px;color:var(--tan);margin-top:14px}
.card-value{font-size:21px;color:var(--green);margin-top:2px}
.card-potato{left:111px}
.card-maize{left:448px}
.card-wheat{left:785px}

/* footer */
.footer-brand{left:113px;top:2220px;display:flex;align-items:center;gap:14px}
.footer-brand .brand-dot{width:22px;height:22px}
.footer-brand .brand-name{font-size:34px}
.footer-heading{font-family:"Merriweather",Georgia,serif;font-weight:700;font-size:22px;color:var(--green)}
.footer-list{list-style:none;font-size:16px;color:var(--text)}
.footer-list li{height:38.7px}
.quick-heading{left:539px;top:2137px}
.quick-list{left:539px;top:2186px}
.other-heading{left:920px;top:2139px}
.other-list{left:920px;top:2188px}
.footer-line{top:2442px;height:2px;width:255px;background:var(--tan)}
.copyright{left:0;width:1200px;top:2427px;text-align:center;font-size:14.5px;color:var(--text)}
</style>
</head>
<body>

<header>
  <div class="abs brand"><span class="brand-dot"></span><span class="brand-name">Harvest Crest Oruva</span></div>

  <div class="abs contact call">
    <div class="contact-icon">
      <svg width="22" height="22" viewBox="0 0 24 24"><path fill="#fff" d="M6.6 10.8a15.1 15.1 0 0 0 6.6 6.6l2.2-2.2a1 1 0 0 1 1-.25 11.4 11.4 0 0 0 3.6.57 1 1 0 0 1 1 1V20a1 1 0 0 1-1 1A17 17 0 0 1 3 4a1 1 0 0 1 1-1h3.5a1 1 0 0 1 1 1c0 1.25.2 2.45.57 3.57a1 1 0 0 1-.25 1z"/></svg>
    </div>
    <div><div class="contact-label">Call Us</div><div class="contact-value">+ 1 555 014 2290</div></div>
  </div>

  <div class="abs contact mail">
    <div class="contact-icon">
      <svg width="22" height="18" viewBox="0 0 24 18"><rect x="1" y="1" width="22" height="16" rx="2" fill="#fff"/><path d="M2 2l10 8 10-8" stroke="#0b6b3a" stroke-width="2" fill="none"/></svg>
    </div>
    <div><div class="contact-label">Email</div><div class="contact-value">hello@hcoruva.org</div></div>
  </div>

  <nav>
    <span class="abs nav" style="left:492px">Home</span>
    <span class="abs nav" style="left:557px">Food Security</span>
    <span class="abs nav" style="left:671px">Farmer Empowerment &amp; Education</span>
    <span class="abs nav active" style="left:920px">Sustainability</span>
    <span class="abs nav" style="left:1036px">Contact Us</span>
  </nav>
</header>

<section>
  <div class="abs hero" role="img" aria-label="Smiling farmer carrying a crate of fresh vegetables on a green farm track"></div>
  <div class="abs hero-kicker">Welcome To</div>
  <div class="abs hero-title">Sustainability</div>
  <div class="abs play"><svg width="22" height="24" viewBox="0 0 22 24"><path d="M4 2l16 10L4 22z" fill="#fff"/></svg></div>
</section>

<section>
  <h1 class="abs section-title">Sustainability</h1>
  <div class="abs rule"></div>

  <div class="abs photo photo-one" role="img" aria-label="Farmer holding a crate of leafy greens in a crop field"></div>
  <h2 class="abs sub-heading solutions-title">Sustainable Solutions</h2>
  <p class="abs copy solutions-copy">All irrigation, cropping and production facilities will be operated “off grid” using extensive solar and hydroelectric power generation. In addition, cropping at all sites will be supported with the use of drones for spraying and crop analysis resulting in significant fuel savings and the associated carbon output.</p>

  <h2 class="abs sub-heading processing-title">Processing Facilities</h2>
  <p class="abs copy processing-copy">Each of the allocated production zones will be furnished with handling, processing and milling facilities for all crops produced as part of the program. These will include Potatoes, Maize and Wheat.Harvest Crest Oruva will undertake primary production of the food goods and market them into the Namibian food supply chain.</p>
  <h3 class="abs yields-title">Anticipated yields per production zone:</h3>
  <div class="abs photo photo-two" role="img" aria-label="Two smiling farmers holding crates of fresh vegetables"></div>
</section>

<section>
  <div class="abs field" role="img" aria-label="Rows of young green crops in a field"></div>

  <div class="abs card card-potato">
    <svg width="92" height="84" viewBox="0 0 92 84" fill="none" stroke="#0b6b3a" stroke-width="2.5">
      <path d="M30 6c14-4 26 6 26 18 0 6-4 10-10 12-10 4-14 16-24 20C12 60 4 52 4 42 4 28 16 10 30 6z"/>
      <path d="M40 38c16-8 44-4 46 14 2 16-16 26-34 24C36 74 26 66 28 54c1-8 6-13 12-16z"/>
      <circle cx="26" cy="20" r="1.5"/><circle cx="18" cy="36" r="1.5"/><circle cx="52" cy="52" r="1.5"/><circle cx="66" cy="60" r="1.5"/>
    </svg>
    <div class="card-title">Potatoes</div>
    <div class="card-value">20,000 Ton Per Annum</div>
  </div>

  <div class="abs card card-maize">
    <svg width="84" height="80" viewBox="0 0 84 80" fill="none" stroke="#0b6b3a" stroke-width="2.5">
      <path d="M6 8c6-6 20-4 22 4 1 6-6 12-12 10C8 20 2 14 6 8z"/>
      <path d="M58 16c8-2 16 4 14 12-2 6-10 8-16 4-4-4-4-14 2-16z"/>
      <path d="M34 36c6-6 18-2 16 6-1 6-10 10-16 6-3-3-3-9 0-12z"/>
      <path d="M6 52c6-4 16 0 14 8-2 6-10 8-14 4-4-4-4-9 0-12z"/>
      <path d="M40 60c8-4 18 2 14 10-3 6-12 6-16 2-3-4-2-10 2-12z"/>
    </svg>
    <div class="card-title">Maize</div>
    <div class="card-value">16,000 Ton Per Annum</div>
  </div>

  <div class="abs card card-wheat">
    <svg width="84" height="84" viewBox="0 0 84 84" fill="none" stroke="#0b6b3a" stroke-width="2.5">
      <path d="M60 8A38 38 0 1 0 78 34"/><circle cx="70" cy="14" r="3"/>
      <path d="M42 70V24"/>
      <path d="M42 34c-6-2-10-6-10-12 6 0 10 4 10 10zM42 34c6-2 10-6 10-12-6 0-10 4-10 10z"/>
      <path d="M42 48c-7-2-12-7-12-13 7 0 12 5 12 11zM42 48c7-2 12-7 12-13-7 0-12 5-12 11z"/>
      <path d="M42 24c-3-4-3-8 0-12 3 4 3 8 0 12z"/>
    </svg>
    <div class="card-title">Wheat</div>
    <div class="card-value">6,000 Ton Per Annum</div>
  </div>
</section>

<footer>
  <div class="abs footer-brand"><span class="brand-dot"></span><span class="brand-name">Harvest Crest Oruva</span></div>

  <h4 class="abs footer-heading quick-heading">Quick Links</h4>
  <ul class="abs footer-list quick-list">
    <li>Home</li><li>Food Security</li><li>Farmer Empowerment and Education</li><li>Sustainability</li><li>Contact Us</li>
  </ul>

  <h4 class="abs footer-heading other-heading">Other Links</h4>
  <ul class="abs footer-list other-list">
    <li>Terms and conditions</li><li>Privacy policy</li><li>Career</li><li>Help center</li><li>Support</li>
  </ul>

  <div class="abs footer-line" style="left:113px"></div>
  <div class="abs footer-line" style="left:834px"></div>
  <p class="abs copyright">Copyright © 2024&nbsp; Harvest Crest Oruva. All rights reserved.</p>
</footer>

</body>
</html>
```